San Francisco Leading Consulting firm - 47Vora Web Design Project

•Create a Web Design
•Uncoded webpage layout design
•2 Pages Design - Homepage + Interior Page

Task Description
Hello, we're looking for a re-design our current website www.47vora-example.com

we have a sample mockup design @

http://47vora.pubtrellis-example.org/

This shows the layout that we like and also a sample of 6 pictures that would change based on where you mouse over..

6 pictures HOME design needs to be included.

SMART
THOUGHTFUL
FLEXIBLE
CREATIVE SERVICES
TECHNICAL SERVICES
PARTNERS

sites we like:

http://www.melvanadvisory-example.com/Home.cfm?id=Home
http://www.plinthworks-example.com/index.html

Our company can be best described as: 100+ employees, cutting-edge, depandable, innovative, strong, smart.

Our Primary focus is: IT Consulting Services and Creative Design services

47Vora LLC is a consulting firm providing creative design, business and technology solutions to both private and public interests.

Established in 1996, 47Vora is a San Francisco based company providing specialists for a range of business needs including:

Creative Design Services
•Print
•Logo Design
•Website Design
•Illustration

and

Business and Technology solutions

•Application Software and Web Development
•Business Process Re-Design (BPR)
•Business/Systems Analysis and Requirement Documentation
•Mentoring and Training
•Network/Hardware Installation Services
•System Design and Architecture
•Vendor Management
•Docuvault Architecture and Implementation

our sample mockup site:

Reason: Due to holiday season, we're not available to work with designers and finilize our design.  

Thank you very much for submitting your design.

We appreciate your time and creativity.   Since, our office is currently closed for holidays, we will be reviewing it in details next week and will make our decision as soon as possible.

It would be great if you could submit any of your changes by Wed next week, so it would be part of our reviews. 

Please see updated wireframe under attachments:  we have some minor updates to our wireframe that we would like you to update your designs, if possible.  

We also encorouge you not to use our standard wireframe and come up with more unique designs.   Everything would be considered when we review your design.

 

Target Market(s)

Creative services and professional services clients, including government agencies

Industry/Entity Type

Business

Requirements
Must have
• Clean, professional look, easy navigation

```html
<!DOCTYPE html>
<html lang="en">
<head>
<meta charset="utf-8">
<title>47Vora — Home</title>
<link rel="stylesheet" href="https://fonts.googleapis.com/css2?family=Open+Sans:wght@400;600&family=Archivo+Black&display=swap">
<style>
:root{
  --blue:#0a93c9;
  --blue-dark:#0679ab;
  --ink:#1e1e1e;
  --bar:#2a2a2a;
  --strip:#4b4b4b;
  --rule:#b9b9b9;
  --white:#ffffff;
  --logo-grey:#555b60;
}
*{box-sizing:border-box;margin:0;padding:0}
html,body{width:1200px;height:900px;overflow:hidden;background:var(--white);font-family:"Open Sans",Arial,sans-serif;color:var(--ink)}
.page{position:relative;width:1200px;height:900px}

.brand{position:absolute;left:133px;top:24px;display:flex;align-items:center;gap:10px}
.brand-dot{width:30px;height:30px;border-radius:50%;background:var(--blue)}
.brand-name{font-size:28px;font-weight:400;color:var(--logo-grey);letter-spacing:1px}

.login{position:absolute;left:984px;top:0;width:93px;height:41px;border-radius:0 0 4px 4px;background:linear-gradient(#3a3a3a,#141414);border-top:7px solid var(--blue);color:var(--white);font-size:14px;text-align:center;line-height:33px}

.nav-bar{position:absolute;left:0;top:94px;width:1200px;height:38px;background:linear-gradient(#3a3a3a,#1f1f1f)}
.nav-line{position:absolute;left:118px;top:131px;width:1082px;height:2px;background:var(--blue)}
.nav-line::before{content:"";position:absolute;left:0;top:0;width:960px;height:6px;background:var(--blue);border-radius:0 0 3px 3px}
.nav{position:absolute;left:118px;top:89px;height:43px;display:flex;list-style:none}
.nav li{height:43px;padding-top:5px;border-right:1px solid #111;box-shadow:1px 0 0 #4a4a4a;color:var(--white);font-size:14px;display:flex;align-items:center;justify-content:center;gap:8px}
.nav li.active{background:var(--blue);border-radius:4px 4px 0 0;border-right:0;box-shadow:none}
.nav .chev{width:8px;height:12px}

.hero{position:absolute;left:118px;top:149px;width:960px;height:378px;background:#000;overflow:hidden}
.hero-art{position:absolute;inset:0;background:radial-gradient(ellipse 70% 18% at 50% 62%,rgba(120,170,215,.75),rgba(40,80,130,.35) 55%,transparent 80%),linear-gradient(170deg,#000 35%,#0d1d30 70%,#1c3350 100%)}
.hero-title{position:absolute;left:398px;top:60px;font-family:"Archivo Black",Arial,sans-serif;font-size:44px;font-weight:400;color:var(--white);line-height:1;white-space:nowrap}
.hero-link{position:absolute;left:400px;top:112px;display:flex;align-items:center;gap:10px;font-family:"Archivo Black",Arial,sans-serif;font-size:22px;color:var(--blue);white-space:nowrap}
.hero-arrow{position:absolute;top:163px;width:30px;height:30px}
.hero-arrow.prev{left:12px}
.hero-arrow.next{left:913px}

.thumbs{position:absolute;left:118px;top:527px;width:960px;height:83px;background:var(--strip);border-radius:0 0 4px 4px}
.thumb{position:absolute;top:14px;width:160px;height:60px}
.thumb.selected{box-shadow:0 0 6px 3px rgba(255,250,200,.75)}
.t1{left:44px;background:radial-gradient(circle at 40% 45%,#d5401a 0,#3a4ab0 12%,#0e1d5a 60%,#050a20)}
.t2{left:220px;background:linear-gradient(90deg,#f2f2f2,#fff 60%,#e6e6e6)}
.t3{left:399px;background:linear-gradient(90deg,#6a6e72,#c9cfd3 50%,#8b9298)}
.t4{left:577px;background:linear-gradient(90deg,#6f7b80,#a9b3b7 60%,#c5cbce)}
.t5{left:755px;background:linear-gradient(170deg,#000 30%,#234060 55%,#000 85%)}

.features{position:absolute;left:118px;top:649px;width:960px;height:171px;display:flex}
.feature{position:relative;height:171px}
.feature + .feature{border-left:1px solid var(--rule)}
.f1{width:311px;padding-left:7px}
.f2{width:334px;padding-left:19px}
.f3{width:315px;padding-left:16px}
.feature h2{display:flex;align-items:center;gap:12px;font-size:17.5px;font-weight:400;height:28px;margin-bottom:8px}
.f1 h2{gap:18px}
.f3 h2{gap:19px}
.feature h2 svg{width:24px;height:24px}
.feature p{font-size:12.5px;line-height:24px;letter-spacing:0;width:305px}
.btn{position:absolute;width:109px;height:23px;border-radius:3px;background:linear-gradient(var(--blue),var(--blue-dark));color:var(--white);font-size:13.5px;text-align:center;line-height:23px;letter-spacing:.3px}
.f1 .btn{left:5px;top:145px}
.f2 .btn{left:17px;top:146px}
.f3 .btn{left:16px;top:103px}

.footer{position:absolute;left:0;top:852px;width:1200px;height:48px;background:var(--bar);color:var(--white);font-size:12.5px;text-align:center;line-height:28px;letter-spacing:.2px}
</style>
</head>
<body>
<div class="page">
  <header>
    <div class="brand"><span class="brand-dot"></span><span class="brand-name">47VORA</span></div>
    <div class="login">LOGIN</div>
  </header>

  <div class="nav-bar"></div>
  <div class="nav-line"></div>
  <ul class="nav">
    <li class="active" style="width:111px">HOME</li>
    <li style="width:144px">COMPANY <svg class="chev" viewBox="0 0 8 12"><path d="M1.5 1l5 5-5 5" fill="none" stroke="#fff" stroke-width="2.2"/></svg></li>
    <li style="width:199px">TECHNICAL SERVICES <svg class="chev" viewBox="0 0 8 12"><path d="M1.5 1l5 5-5 5" fill="none" stroke="#fff" stroke-width="2.2"/></svg></li>
    <li style="width:194px">CREATIVE SERVICES <svg class="chev" viewBox="0 0 8 12"><path d="M1.5 1l5 5-5 5" fill="none" stroke="#fff" stroke-width="2.2"/></svg></li>
    <li style="width:135px">PARTNERS <svg class="chev" viewBox="0 0 8 12"><path d="M1.5 1l5 5-5 5" fill="none" stroke="#fff" stroke-width="2.2"/></svg></li>
    <li style="width:138px">CONTACT US</li>
  </ul>

  <section class="hero">
    <div class="hero-art" role="img" aria-label="Flowing streaks of blue light across a black background"></div>
    <h1 class="hero-title">CREATIVE SERVICES</h1>
    <div class="hero-link">View our featured work
      <svg width="34" height="28" viewBox="0 0 34 28"><path d="M2 2l12 12-12 12h8l12-12L10 2zM14 2l12 12-12 12h8l12-12L22 2z" fill="#0a93c9"/></svg>
    </div>
    <svg class="hero-arrow prev" viewBox="0 0 30 30"><circle cx="15" cy="15" r="15" fill="#e6e9ec"/><path d="M7 15l7-7v4.5h9v5h-9V22z" fill="#2a3440"/></svg>
    <svg class="hero-arrow next" viewBox="0 0 30 30"><circle cx="15" cy="15" r="15" fill="#e6e9ec"/><path d="M23 15l-7-7v4.5H7v5h9V22z" fill="#2a3440"/></svg>
  </section>

  <div class="thumbs">
    <div class="thumb t1" role="img" aria-label="Glowing blue network of fibres with an orange spark"></div>
    <div class="thumb t2 selected" role="img" aria-label="Businessman bending over a laptop on a white floor"></div>
    <div class="thumb t3" role="img" aria-label="Person crouched in a busy city crowd"></div>
    <div class="thumb t4" role="img" aria-label="Chalkboard covered in formulas"></div>
    <div class="thumb t5 selected" role="img" aria-label="Blue light streaks on black"></div>
  </div>

  <section class="features">
    <div class="feature f1">
      <h2><svg viewBox="0 0 24 24"><rect x="4" y="4" width="16" height="11" fill="none" stroke="#1e1e1e" stroke-width="2"/><path d="M1 18h22v2H1z" fill="#1e1e1e"/></svg>For Graphic Designers</h2>
      <p>47Vora is looking for top creative talent to deliver graphic design solutions for some leading global brands Do you have what it takes?</p>
      <div class="btn">Learn More</div>
    </div>
    <div class="feature f2">
      <h2><svg viewBox="0 0 24 24"><g fill="#1e1e1e" stroke="#1e1e1e" stroke-width="2"><path d="M12 12L12 3M12 12L4 17M12 12L20 17"/><circle cx="12" cy="12" r="2.5"/><circle cx="12" cy="3" r="2"/><circle cx="4" cy="17" r="2"/><circle cx="20" cy="17" r="2"/></g></svg>The 47Vora Difference</h2>
      <p>Smart, Flexible, Thoughtful: find out why leading corporations and government agencies are turning to 47vora to help manage their most demanding IT services challenges.</p>
      <div class="btn">Learn More</div>
    </div>
    <div class="feature f3">
      <h2><svg viewBox="0 0 24 24"><circle cx="12" cy="7.5" r="5.5" fill="#1e1e1e"/><path d="M1 23c0-6 5-9 11-9s11 3 11 9z" fill="#1e1e1e"/></svg>Team Up With the Best</h2>
      <p>When it comes to technology partnerships, our mission it so make you a success.</p>
      <div class="btn">Learn More</div>
    </div>
  </section>

  <footer class="footer">Copyright 2010, 47Vora, LLC All rights reserved.</footer>
</div>
</body>
</html>
```